Exciting opportunity to create logo and a label for our natural health brand.

About us

We are a customer centric health supplement brand who believes in natural medicine and high quality ingredients. We take a holistic approach to healthcare, with an eastern philosophy. We believe in being partners with our customers in their health care journey and are invested in their well being.

Our brand philosophy and values are attached (see Vorna philosophy.png). Our personality traits are:

- Natural
- Fresh
- Modern
- Balanced (in a holistic sense)

Task breakdown

1. Design a fresh feeling logo for us
- We want it to represent our values and high quality ingredients. We would like the quality of the product to be reflected in the branding and have a high end feel.
- Logo text must include Vorna Health Sciences
- We want the Vorna to be the focus of the logo (see uploaded image Vorna logo example.png)
The logo does not have to follow this layout, but we just want the Vorna to stand out. Feel free to use your creative license on this!

2. Create an attractive label to go on the supplement bottle
- The designs need to be eye catching, give a sense of high end ingredients and natural products and tie in with the logo to give a joined up feel.
- We are selling our products online and need them to really stand out from the competition.
- See examples of labels and packaging we like (1 -7 label design).

The initial label we would like you to design would be for our product Calm Drift. It is a product that assists in the management of Anxiety and stress. The label will appear on the bottle that holds the capsules for this supplement, see uploaded files (Example plain bottles.png). The bottles may be white as the picture shows or dark blue recyclable plastic or dark brown glass . We don't have the exact dimensions of the bottle yet, but I will follow up with these.

The label needs to include the following things:
1. The logo
2. The name of the product
3. The product is to help with the relief of Anxiety and Stress
4. Number of capsules the bottle contains
5. The back of the label should have
i) The ingredients
ii) Dosage
iii) Directions of use

Please use placeholder text where needed.

We look forward to seeing your design. Thank you.

```html
<!DOCTYPE html>
<html lang="en">
<head>
<meta charset="utf-8">
<title>Vorna Health Sciences – Calm Drift label variants</title>
<link href="https://fonts.googleapis.com/css2?family=Bebas+Neue&family=Poppins:wght@300;400;500;600&display=swap" rel="stylesheet">
<style>
  :root {
    --canvas: #ffffff;
    --label-cream: #f4f0e5;
    --label-cream-light: #faf8f1;
    --ink: #2a2a2a;
    --ink-soft: #3a3a3a;
    --gold-soft: rgba(226, 168, 73, 0.55);
    --gold-mid: rgba(226, 168, 73, 0.75);
    --gold-fade: rgba(226, 168, 73, 0);
  }
  * { box-sizing: border-box; margin: 0; padding: 0; }
  html, body {
    width: 1200px; height: 932px; overflow: hidden;
    background: var(--canvas);
    font-family: "Poppins", sans-serif;
    color: var(--ink);
  }
  .canvas { position: relative; width: 1200px; height: 932px; }

  .label {
    position: absolute; top: 347px;
    width: 329px; height: 386px;
    background: linear-gradient(90deg, var(--label-cream) 0%, var(--label-cream-light) 55%, var(--label-cream) 100%);
    overflow: hidden;
  }
  .label--mono { left: 45px; }
  .label--gold { left: 430px; }
  .label--green { left: 815px; }

  .brand-name {
    position: absolute; left: 56px; top: 48px; width: 112px;
    font-size: 17px; font-weight: 500; line-height: 1.25;
    letter-spacing: 1.5px; text-transform: uppercase;
    color: var(--ink);
  }

  .botanical {
    position: absolute; left: 168px; top: 28px;
    width: 116px; height: 150px;
    border-radius: 60% 40% 55% 45% / 50% 45% 55% 50%;
  }
  .label--mono .botanical { background: radial-gradient(ellipse at 45% 50%, rgba(154,154,154,0.35), rgba(154,154,154,0) 70%); }
  .label--gold .botanical { background: radial-gradient(ellipse at 45% 50%, rgba(224,174,88,0.4), rgba(224,174,88,0) 70%); }
  .label--green .botanical { background: radial-gradient(ellipse at 45% 50%, rgba(127,174,135,0.5), rgba(127,174,135,0) 70%); }

  .product-name {
    position: absolute; left: 54px; top: 208px;
    font-family: "Bebas Neue", sans-serif; font-weight: 400;
    font-size: 58px; line-height: 1; letter-spacing: 0.5px;
    color: var(--ink); white-space: nowrap;
  }

  .ingredient-band {
    position: absolute; left: 50px; top: 265px;
    width: 224px; height: 28px;
    display: flex; align-items: center; padding-left: 5px;
    background: linear-gradient(90deg, var(--gold-fade) 0%, var(--gold-soft) 8%, var(--gold-mid) 50%, var(--gold-soft) 92%, var(--gold-fade) 100%);
    font-size: 13px; letter-spacing: 1px; color: var(--ink);
    white-space: nowrap;
  }
  .ingredient-band--light { font-weight: 300; letter-spacing: 0.5px; }

  .benefit {
    position: absolute; left: 57px; top: 303px;
    font-size: 13.5px; letter-spacing: 1.6px; line-height: 22px;
    color: var(--ink);
  }
  .benefit__strong { font-weight: 600; }

  .info-band {
    position: absolute; left: 0; top: 350px;
    width: 100%; height: 23px;
    display: flex; align-items: center; padding-left: 57px;
    background: linear-gradient(90deg, var(--gold-soft) 0%, var(--gold-mid) 50%, var(--gold-soft) 100%);
    font-size: 10.5px; font-weight: 300; letter-spacing: 1.3px;
    color: var(--ink); white-space: nowrap;
  }
  .info-band__divider { margin: 0 6px; font-weight: 400; }
</style>
</head>
<body>
<main class="canvas">

  <section class="label label--mono">
    <p class="brand-name">Vorna Health Sciences</p>
    <div class="botanical" role="img" aria-label="Line-drawn leafy branch illustration in grey"></div>
    <h1 class="product-name">CALM DRIFT</h1>
    <div class="ingredient-band">Vitamins · Minerals · Herbs</div>
    <p class="benefit">RELIEF OF<br><span class="benefit__strong">ANXIETY</span> AND <span class="benefit__strong">STRESS</span></p>
    <div class="info-band">60 CAPSULES<span class="info-band__divider">|</span>DIETARY SUPPLEMENT</div>
  </section>

  <section class="label label--gold">
    <p class="brand-name">Vorna Health Sciences</p>
    <div class="botanical" role="img" aria-label="Line-drawn leafy branch illustration in gold"></div>
    <h1 class="product-name">CALM DRIFT</h1>
    <div class="ingredient-band ingredient-band--light">Vitamins · Minerals · Herbs</div>
    <p class="benefit">RELIEF OF<br><span class="benefit__strong">ANXIETY</span> AND <span class="benefit__strong">STRESS</span></p>
    <div class="info-band">60 CAPSULES<span class="info-band__divider">|</span>DIETARY SUPPLEMENT</div>
  </section>

  <section class="label label--green">
    <p class="brand-name">Vorna Health Sciences</p>
    <div class="botanical" role="img" aria-label="Leafy branch illustration with soft green watercolour fill"></div>
    <h1 class="product-name">CALM DRIFT</h1>
    <div class="ingredient-band">Vitamins · Minerals · Herbs</div>
    <p class="benefit">RELIEF OF<br><span class="benefit__strong">ANXIETY</span> AND <span class="benefit__strong">STRESS</span></p>
    <div class="info-band">60 CAPSULES<span class="info-band__divider">|</span>DIETARY SUPPLEMENT</div>
  </section>

</main>
</body>
</html>
```